Private Investment Firm Needs PowerPoint Presentation Template

Design PowerPoint template, take Pinebrook-submitted rough presentation draft, and drop it into new template. See attached Project Brief file for more detail.
Updates

Some decent designs have been submitted but they seem to lack the understanding of our target markets. I am hopeful that more time and feedback will result in better results.

Target Market(s)

Private company owners and intermediaries.

Font styles to use
Serif

Colors
3176b5

Requirements
Must have
• See attached Project Brief.
Nice to have
Should not have
• No B2C fluff--this is a B2B project.

```html
<!DOCTYPE html>
<html lang="en">
<head>
<meta charset="utf-8">
<title>Pinebrook Capital – Contact</title>
<link rel="stylesheet" href="https://fonts.googleapis.com/css2?family=Montserrat:wght@300;400;700&display=swap">
<style>
  :root {
    --blue: #1a62ad;
    --blue-dark: #0f6fbf;
    --blue-light: #3196d0;
    --charcoal: #555555;
    --text: #3d3d3d;
    --line: #9a9a9a;
    --paper-top: #ffffff;
    --paper-bottom: #ececec;
  }
  * { margin: 0; padding: 0; box-sizing: border-box; }
  html, body { width: 1200px; height: 770px; overflow: hidden; background: #ffffff; }
  .slide {
    position: relative;
    width: 1200px;
    height: 770px;
    overflow: hidden;
    font-family: "Montserrat", sans-serif;
    background: linear-gradient(160deg, var(--paper-top) 0%, var(--paper-bottom) 100%);
  }
  .slide-shapes { position: absolute; inset: 0; }
  .title {
    position: absolute;
    left: 436px; top: 46px; width: 310px; height: 58px;
    display: flex; align-items: center; justify-content: center;
    color: #ffffff; font-weight: 400; font-size: 44px; letter-spacing: 1px;
  }
  .contact-list { position: absolute; left: 154px; top: 152px; }
  .contact-entry { position: absolute; left: 0; white-space: nowrap; }
  .contact-entry h2 {
    color: var(--blue); font-weight: 700; font-size: 22px; line-height: 30px; margin-bottom: 4px;
  }
  .contact-entry p { color: var(--text); font-weight: 400; font-size: 21px; line-height: 26.5px; }
  .contact-entry .accent { color: var(--blue); }
  .contact-entry .strong { color: var(--blue); font-weight: 700; }
  .entry-principal { top: 0; }
  .entry-boston { top: 225px; }
  .entry-sf { top: 400px; }
  .portrait {
    position: absolute; left: 863px; top: 424px; width: 256px; height: 256px;
    border-radius: 50%; border: 4px solid #ffffff;
    background: radial-gradient(circle at 50% 40%, #c9d3dc 0%, #b5c1cc 55%, #2b3347 100%);
  }
  .brand {
    position: absolute; left: 716px; top: 686px;
    display: flex; align-items: center; gap: 10px;
    color: var(--blue); font-weight: 400; font-size: 20px; letter-spacing: 2px;
  }
  .brand-mark { width: 34px; height: 34px; border-radius: 50%; background: var(--blue); }
  .website { position: absolute; left: 114px; top: 715px; font-size: 19px; color: var(--text); }
  .website .strong { color: var(--blue); font-weight: 700; }
  .page-number {
    position: absolute; left: 1131px; top: 720px; color: #ffffff; font-weight: 700; font-size: 17px;
  }
</style>
</head>
<body>
<div class="slide">
  <svg class="slide-shapes" width="1200" height="770" viewBox="0 0 1200 770">
    <defs>
      <linearGradient id="side-blue" x1="0" y1="0" x2="0" y2="1">
        <stop offset="0" stop-color="var(--blue-dark)"/>
        <stop offset="1" stop-color="var(--blue-light)"/>
      </linearGradient>
    </defs>
    <polygon class="side-band-left" points="0,0 120,0 0,568" fill="var(--charcoal)"/>
    <polygon class="side-band-right" points="1121,0 1200,0 1200,770 909,770" fill="url(#side-blue)"/>
    <polygon class="title-slash" points="421,46 434,46 420,104 407,104" fill="var(--charcoal)"/>
    <polygon class="title-band" points="450,46 745,46 730,104 436,104" fill="var(--blue)"/>
    <polygon class="title-slash" points="760,46 773,46 759,104 746,104" fill="var(--charcoal)"/>
    <line class="timeline" x1="114" y1="170" x2="114" y2="666" stroke="var(--line)" stroke-width="1.5"/>
    <g class="timeline-dots" fill="#ffffff" stroke="var(--blue)" stroke-width="1.5">
      <circle cx="114" cy="165" r="8"/>
      <circle cx="114" cy="390" r="8"/>
      <circle cx="114" cy="565" r="8"/>
    </g>
    <g fill="var(--blue)">
      <circle cx="114" cy="165" r="4"/>
      <circle cx="114" cy="390" r="4"/>
      <circle cx="114" cy="565" r="4"/>
    </g>
  </svg>

  <div class="title">CONTACT</div>

  <div class="contact-list">
    <div class="contact-entry entry-principal">
      <h2>Daniel R. Marchetti</h2>
      <p>Principal</p>
      <p>41 Alder Ridge Road, Suite 210</p>
      <p>Milford, CT&nbsp; 06460</p>
      <p>Direct: (555) 410-2219</p>
      <p>dmarchetti@<span class="strong">pinebrookcapital</span>.com</p>
    </div>
    <div class="contact-entry entry-boston">
      <h2>Boston Office</h2>
      <p>12 Harbor Lane, Suite 300</p>
      <p>Salem, MA 01970</p>
      <p class="accent">(555) 410-2200</p>
    </div>
    <div class="contact-entry entry-sf">
      <h2>San Francisco Office</h2>
      <p>Two Market Plaza, Suite 820</p>
      <p>San Francisco, CA 94105</p>
      <p class="accent">(555) 382-1400</p>
    </div>
  </div>

  <div class="portrait" role="img" aria-label="Portrait photo of the principal in a dark blazer"></div>

  <div class="brand">
    <span class="brand-mark"></span>
    <span>PINEBROOK CAPITAL</span>
  </div>

  <div class="website">www.<span class="strong">pinebrookcapital</span>.com</div>
  <div class="page-number">4.</div>
</div>
</body>
</html>
```